Business Card Design Project

Doctor, Pain Management. Need a new business card design with appointment info on the back. New address is 18 Corvell Road, Suite 304, Brisdale, NJ 07391. Right now I believe the rest of the information is staying the same.

```html
<!DOCTYPE html>
<html lang="en">
<head>
<meta charset="utf-8">
<title>Gentle Relief Pain Management – Business Card</title>
<link rel="stylesheet" href="https://fonts.googleapis.com/css2?family=Cormorant+Garamond:wght@500;600&family=Open+Sans:ital,wght@0,400;1,400&display=swap">
<style>
  :root {
    --backdrop: #d9d4cc;
    --card-black: #141516;
    --card-black-edge: #232526;
    --band-dark: #23221a;
    --paper: #ffffff;
    --name-blue: #5fb8d8;
    --title-lime: #c9d03a;
    --contact-white: #e9ecee;
    --ink: #2b2b2b;
    --rule: #777;
    --ornament-olive: #4a4a2e;
    --ornament-dot: #3f5867;
  }
  * { box-sizing: border-box; margin: 0; padding: 0; }
  html, body { width: 1200px; height: 950px; overflow: hidden; }
  body { background: var(--backdrop); position: relative; }

  .card {
    position: absolute;
    left: 300px;
    width: 600px;
    height: 343px;
    border-radius: 4px;
    overflow: hidden;
    box-shadow: 0 6px 18px rgba(0,0,0,.25);
  }

  /* Front */
  .card-front {
    top: 100px;
    background: linear-gradient(135deg, var(--card-black-edge) 0%, var(--card-black) 60%);
    font-family: "Cormorant Garamond", Georgia, serif;
  }
  .spine-ornament {
    position: absolute;
    left: 40px; top: 70px;
    width: 380px; height: 200px;
    border-radius: 50%;
    background: radial-gradient(ellipse at center, rgba(74,74,46,.55) 0%, rgba(63,88,103,.3) 45%, rgba(20,21,22,0) 72%);
  }
  .doctor-name {
    position: absolute;
    left: 270px; top: 34px;
    color: var(--name-blue);
    font-size: 25px;
    font-weight: 500;
    letter-spacing: .5px;
  }
  .doctor-title {
    position: absolute;
    left: 300px; top: 66px;
    color: var(--title-lime);
    font-size: 19px;
    font-weight: 500;
  }
  .contact-list {
    position: absolute;
    left: 36px; bottom: 30px;
    list-style: none;
    color: var(--contact-white);
    font-size: 16px;
    line-height: 23px;
  }

  /* Back */
  .card-back {
    top: 507px;
    background: var(--paper);
    font-family: "Open Sans", Arial, sans-serif;
    color: var(--ink);
  }
  .appointment-form {
    position: absolute;
    left: 34px; top: 34px;
    width: 380px;
    font-size: 15px;
  }
  .form-row {
    display: flex;
    align-items: flex-end;
    margin-bottom: 22px;
  }
  .form-row .label { white-space: nowrap; margin-right: 6px; }
  .form-row .fill-line {
    flex: 1;
    border-bottom: 1.5px dotted var(--rule);
    height: 16px;
  }
  .form-row .suffix { font-size: 11px; margin-left: 4px; }
  .time-row { margin-left: 150px; }
  .day-list {
    display: flex;
    justify-content: space-between;
    list-style: none;
    margin-bottom: 26px;
  }
  .day-list li { display: flex; align-items: center; gap: 4px; }
  .checkbox {
    width: 13px; height: 13px;
    border: 1.3px solid var(--ink);
    display: inline-block;
  }
  .policy-note {
    font-style: italic;
    font-size: 13px;
    line-height: 20px;
  }
  .brand-band {
    position: absolute;
    right: 0; top: 0;
    width: 170px; height: 100%;
    background: var(--band-dark);
    display: flex;
    flex-direction: column;
    align-items: center;
    justify-content: center;
    gap: 12px;
    padding: 0 16px;
    text-align: center;
  }
  .brand-dot {
    width: 30px; height: 30px;
    border-radius: 50%;
    background: var(--name-blue);
  }
  .brand-name {
    font-family: "Cormorant Garamond", Georgia, serif;
    font-weight: 600;
    font-size: 19px;
    line-height: 22px;
    color: var(--title-lime);
  }
</style>
</head>
<body>

  <section class="card card-front" aria-label="Business card front">
    <div class="spine-ornament" role="img" aria-label="Faint spine ornament with curved line and dots"></div>
    <h1 class="doctor-name">MARA DELVIN, M.D., PH.D.</h1>
    <p class="doctor-title">Board Certified Anesthesiologist</p>
    <ul class="contact-list">
      <li>P. 973.555.0142</li>
      <li>M. 973.555.0187</li>
      <li>clearpathpms.service@gmail.com</li>
      <li>www.gentlereliefpm.com</li>
      <li>18 Corvell Road, Suite 304, Brisdale, NJ 07391</li>
    </ul>
  </section>

  <section class="card card-back" aria-label="Business card back, appointment reminder">
    <div class="appointment-form">
      <div class="form-row">
        <span class="label">Name:</span><span class="fill-line"></span>
      </div>
      <div class="form-row time-row">
        <span class="label">Time:</span><span class="fill-line"></span><span class="suffix">AM/PM</span>
      </div>
      <ul class="day-list">
        <li>Mon <span class="checkbox"></span></li>
        <li>Tue <span class="checkbox"></span></li>
        <li>Wed <span class="checkbox"></span></li>
        <li>Thu <span class="checkbox"></span></li>
        <li>Fri <span class="checkbox"></span></li>
        <li>Sat <span class="checkbox"></span></li>
      </ul>
      <p class="policy-note">Please give 24 hours notice if you are unable to keep your appointment or a cancellation fee may be charged.</p>
    </div>
    <div class="brand-band">
      <span class="brand-dot"></span>
      <p class="brand-name">Gentle Relief Pain Management</p>
    </div>
  </section>

</body>
</html>
```